Roofing Contractor business card redesign

I want to redesign my business card with a fresh, eye catching concept

Target Market(s)

Residential Roofing Clients, potential employees, and subcontractors.

Industry/Entity Type

Business

Colors

Designer to choose colors to be used in the design.

Requirements
Nice to have
• I just want something that's more pleasing to the eye. You can use a combination of either / or of my logos.

```html
<!DOCTYPE html>
<html lang="en">
<head>
<meta charset="utf-8">
<title>Fair Hands General Contractors – Business Card</title>
<link rel="stylesheet" href="https://fonts.googleapis.com/css2?family=Oswald:wght@500;600&family=Source+Sans+3:wght@400;700&display=swap">
<style>
  :root {
    --brown: #4a1410;
    --orange: #e87125;
    --white: #ffffff;
    --backdrop: #ececea;
  }
  * { box-sizing: border-box; margin: 0; padding: 0; }
  html, body { width: 1200px; height: 900px; overflow: hidden; }
  body { background: var(--backdrop); position: relative; font-family: "Source Sans 3", sans-serif; }

  .card { position: absolute; overflow: hidden; box-shadow: 0 4px 14px rgba(0,0,0,.18); }

  /* Front */
  .card-front { left: 78px; top: 35px; width: 588px; height: 362px; background: var(--white); }
  .card-front .bands { position: absolute; inset: 0; }
  .brand { position: absolute; left: 0; right: 0; text-align: center; color: var(--brown); }
  .card-front .brand { top: 52px; }
  .brand-name {
    display: inline-flex; align-items: center; gap: 12px;
    font-family: "Oswald", sans-serif; font-weight: 600; font-size: 50px; line-height: 1;
    letter-spacing: -0.5px;
  }
  .brand-dot { width: 38px; height: 38px; border-radius: 50%; background: var(--orange); display: inline-block; }
  .brand-tagline { display: block; font-weight: 700; font-size: 23px; margin-top: 8px; }

  .contact { position: absolute; right: 316px; top: 242px; text-align: right; color: var(--white); font-size: 15.5px; line-height: 21px; }
  .contact li { list-style: none; display: flex; justify-content: flex-end; align-items: center; gap: 5px; }
  .contact svg { width: 12px; height: 12px; fill: var(--white); }
  .divider { position: absolute; left: 294px; top: 218px; width: 1.5px; height: 120px; background: var(--white); }
  .person { position: absolute; left: 312px; top: 216px; color: var(--white); font-size: 15.5px; line-height: 21px; }
  .person-name { font-family: "Oswald", sans-serif; font-weight: 500; font-size: 25px; line-height: 32px; }
  .person-address { margin-top: 8px; }

  /* Back */
  .card-back { left: 388px; top: 505px; width: 567px; height: 352px; background: var(--orange); }
  .card-back .brand { top: 128px; }
</style>
</head>
<body>

<section class="card card-front" aria-label="Business card front">
  <svg class="bands" width="588" height="362" viewBox="0 0 588 362" aria-hidden="true">
    <polygon points="0,173 400,173 378,201 0,201" fill="var(--orange)"/>
    <polygon points="0,203 384,203 413,165 588,165 588,362 0,362" fill="var(--brown)"/>
  </svg>

  <div class="brand">
    <span class="brand-name"><span>Fair Hands</span><span class="brand-dot"></span></span>
    <span class="brand-tagline">General Contractors, Inc.</span>
  </div>

  <ul class="contact">
    <li>(555) 210-4800
      <svg viewBox="0 0 24 24"><path d="M6.6 10.8a15 15 0 0 0 6.6 6.6l2.2-2.2a1 1 0 0 1 1-.25 11.4 11.4 0 0 0 3.6.57 1 1 0 0 1 1 1V20a1 1 0 0 1-1 1A17 17 0 0 1 3 4a1 1 0 0 1 1-1h3.5a1 1 0 0 1 1 1c0 1.25.2 2.45.57 3.57a1 1 0 0 1-.25 1z"/></svg></li>
    <li>(555) 318-7262
      <svg viewBox="0 0 24 24"><path d="M7 1h10a2 2 0 0 1 2 2v18a2 2 0 0 1-2 2H7a2 2 0 0 1-2-2V3a2 2 0 0 1 2-2zm0 3v15h10V4zm5 16.2a1 1 0 1 0 0 .1z"/></svg></li>
    <li>dale@fairhandsgc.com
      <svg viewBox="0 0 24 24"><path d="M2 5h20v14H2zm2 2v.4l8 5.4 8-5.4V7zm0 2.8V17h16V9.8l-8 5.4z"/></svg></li>
    <li>www.FairHandsGC.com
      <svg viewBox="0 0 24 24"><path d="M12 2a10 10 0 1 0 0 20 10 10 0 0 0 0-20zm-1 17.9A8 8 0 0 1 4.2 10.8L9 15.6v1a2 2 0 0 0 2 2zm6.9-2.5A2 2 0 0 0 16 16h-1v-3a1 1 0 0 0-1-1H8v-2h2a1 1 0 0 0 1-1V7h2a2 2 0 0 0 2-2v-.4a8 8 0 0 1 2.9 12.8z"/></svg></li>
  </ul>

  <div class="divider"></div>

  <div class="person">
    <div class="person-name">Dale Morrow</div>
    <div>Stonecrest certified Roof Inspector</div>
    <div>Licensed Property Adjuster</div>
    <div class="person-address">4820 Cedar Ridge Road Suite 110<br>Plano, TX 75093</div>
  </div>
</section>

<section class="card card-back" aria-label="Business card back">
  <div class="brand">
    <span class="brand-name"><span>Fair Hands</span><span class="brand-dot" style="background: var(--brown);"></span></span>
    <span class="brand-tagline">General Contractors, Inc.</span>
  </div>
</section>

</body>
</html>
```